Coastline Premier Retreats Business Card Design

Design a business card for Coastline Premier Retreats. Look at the website for colors and reference. Card should have logo, name, title, office number, mobile number, email, URL and a tagline like, "Luxury Hotel & Resort Email Marketing" (This might change).

https://www.coastlinepremierretreats.example

The rest I will leave up to your imagination.

Contact Information for Business Card

Logo, name, title, office number, mobile number, email, URL and a tagline like, "Luxury Hotel & Resort Email Marketing" (This might change).

```html
<!DOCTYPE html>
<html lang="en">
<head>
<meta charset="utf-8">
<title>Coastline Premier Retreats Business Card</title>
<link rel="stylesheet" href="https://fonts.googleapis.com/css2?family=Montserrat:wght@400;600;800&family=Poppins:wght@400;500&display=swap">
<style>
  :root {
    --orange: #f47206;
    --black: #0b0b0b;
    --charcoal: #151515;
    --white: #ffffff;
    --ink: #111111;
    --rule: #9a9a9a;
    --backdrop: #c4c4c4;
    --emboss: #2c2c2c;
  }
  * { box-sizing: border-box; margin: 0; padding: 0; }
  html, body { width: 1200px; height: 800px; overflow: hidden; }
  body {
    background: var(--backdrop);
    font-family: "Poppins", sans-serif;
    position: relative;
  }
  .card {
    position: absolute;
    top: 245px;
    width: 540px;
    height: 310px;
    overflow: hidden;
    box-shadow: 0 14px 30px rgba(0,0,0,.25);
  }
  .card--front { left: 40px; background: var(--white); border-right: 3px solid var(--orange); border-bottom: 3px solid var(--orange); }
  .card--back { left: 620px; background: var(--charcoal); }

  /* front */
  .brand {
    position: absolute;
    left: 30px; top: 94px;
    display: flex; align-items: center; gap: 10px;
  }
  .brand__mark { width: 14px; height: 14px; background: var(--orange); flex: none; }
  .brand__name {
    font-family: "Montserrat", sans-serif;
    font-weight: 800;
    font-size: 16px;
    line-height: 1.15;
    letter-spacing: .5px;
    color: var(--ink);
    text-transform: uppercase;
    width: 160px;
  }
  .divider {
    position: absolute;
    left: 226px; top: 46px;
    width: 1px; height: 140px;
    background: var(--rule);
  }
  .contact { position: absolute; left: 246px; top: 44px; right: 18px; }
  .contact__name {
    font-family: "Montserrat", sans-serif;
    font-weight: 800;
    font-size: 20px;
    letter-spacing: .5px;
    color: var(--ink);
    text-transform: uppercase;
    white-space: nowrap;
  }
  .contact__title { color: var(--orange); font-size: 14px; margin-bottom: 12px; }
  .contact__row {
    display: flex; align-items: center; gap: 8px;
    font-size: 12px; color: var(--ink); line-height: 1.8;
    white-space: nowrap;
  }
  .contact__row svg { width: 12px; height: 12px; flex: none; }
  .front-band {
    position: absolute; left: 0; right: 0; bottom: 0;
    height: 72px; background: var(--black);
    display: flex; align-items: center; justify-content: center;
  }
  .front-band__url { color: var(--orange); font-size: 15px; letter-spacing: 1.5px; }

  /* back */
  .back-brand {
    position: absolute; left: 0; right: 0; top: 80px;
    display: flex; justify-content: center; align-items: center; gap: 12px;
  }
  .back-brand__mark { width: 16px; height: 16px; background: var(--emboss); }
  .back-brand__name {
    font-family: "Montserrat", sans-serif;
    font-weight: 800;
    font-size: 24px;
    letter-spacing: 1px;
    text-transform: uppercase;
    color: var(--emboss);
  }
  .back-band {
    position: absolute; left: 0; right: 0; bottom: 0;
    height: 86px; background: var(--orange);
    display: flex; align-items: center; justify-content: center;
  }
  .back-band__tagline {
    font-family: "Montserrat", sans-serif;
    font-weight: 800;
    font-size: 16px;
    letter-spacing: 1px;
    text-transform: uppercase;
    color: var(--white);
  }
</style>
</head>
<body>
  <section class="card card--front">
    <div class="brand">
      <span class="brand__mark"></span>
      <span class="brand__name">Coastline Premier Retreats</span>
    </div>
    <div class="divider"></div>
    <div class="contact">
      <p class="contact__name">Daniel Harper</p>
      <p class="contact__title">Managing Director</p>
      <p class="contact__row">
        <svg viewBox="0 0 12 12" aria-hidden="true"><path d="M2.5 1h2l1 2.5-1.3 1a6 6 0 0 0 3.3 3.3l1-1.3 2.5 1v2a1 1 0 0 1-1 1A9.5 9.5 0 0 1 1 2a1 1 0 0 1 1-1z" fill="var(--orange)"/></svg>
        044-555 010 246
      </p>
      <p class="contact__row">
        <svg viewBox="0 0 12 12" aria-hidden="true"><rect x="3" y="0.8" width="6" height="10.4" rx="1" fill="none" stroke="var(--orange)" stroke-width="1.2"/><circle cx="6" cy="9.3" r=".7" fill="var(--orange)"/></svg>
        044-555 010 247
      </p>
      <p class="contact__row">
        <svg viewBox="0 0 12 12" aria-hidden="true"><rect x="0.5" y="2" width="11" height="8" fill="var(--orange)"/><path d="M0.8 2.4 6 6.6l5.2-4.2" fill="none" stroke="var(--white)" stroke-width="1"/></svg>
        info@coastlinepremierretreats.example
      </p>
    </div>
    <div class="front-band">
      <span class="front-band__url">www.coastlinepremierretreats.example</span>
    </div>
  </section>

  <section class="card card--back">
    <div class="back-brand">
      <span class="back-brand__mark"></span>
      <span class="back-brand__name">Coastline Premier Retreats</span>
    </div>
    <div class="back-band">
      <span class="back-band__tagline">Luxury Hotel &amp; Resort Email Marketing</span>
    </div>
  </section>
</body>
</html>
```